zorvan lumet website design

An IT support and IT Security Company - just use dummy text for now for the design. Examples of sites we like the looks and feel of but need it more professional feel are like: www.kelbrovault.uk.com , www.pravok.co.uk, www.quenthardy.com/professional/, www.vur.com, www.melvish.com,

Best to message me if you have any questions

Target Market(s)

small to medium UK based companies that require IT support services

Industry/Entity Type

It Company

Contact Information for Business Card

use dummy name, telephone and email for now, will provide details later.

Logo Text

zorvan lumet (and then below the logo it should say "your IT, networks and security partner")

Coding

Coded - Design and coding required

Number of Pages Required

5+ page

Colors

Designer to choose colors to be used in the design.

Requirements
Must have
• must be professional, yet simple and clear that this is a serious IT support and IT security company.
Nice to have
• 1)The website homepage must have professional quality pictures of IT support or London city skyline or any picture that projects friendly business partners, professionalism and ready to serve.
• 2) Home page needs to include tabs for following pages 'Services' , 'About Us' , 'Contact Us' 'Home'
• 3) Website built customised using wordpress is ideal and easy for us to manage.
• more room for boxed options from homepage (with pic or image in background)
Should not have
• no checkout trolleys or payment options.

```html
<!DOCTYPE html>
<html lang="en">
<head>
<meta charset="utf-8">
<title>Zorvan Lumet — IT Support &amp; Security</title>
<link rel="stylesheet" href="https://fonts.googleapis.com/css2?family=Montserrat:wght@500;600;700&family=Lato:wght@400;700&display=swap">
<style>
:root{
  --blue:#165f82;
  --blue-dark:#124f6d;
  --orange:#f4583a;
  --text:#555c61;
  --white:#ffffff;
  --rule:#e4e7ea;
}
*{box-sizing:border-box;margin:0;padding:0}
html,body{width:1200px;height:3025px;overflow:hidden;background:var(--white)}
body{font-family:'Lato',sans-serif;color:var(--text);position:relative}
a{text-decoration:none}

/* Header */
.site-header{height:125px;position:relative}
.brand{position:absolute;left:80px;top:30px}
.brand-name{font-family:'Montserrat',sans-serif;font-weight:700;font-size:40px;line-height:44px;color:var(--blue);text-transform:uppercase;letter-spacing:1px}
.brand-tagline{margin-top:4px;font-size:14px;line-height:18px;color:var(--text);letter-spacing:.3px}
.header-contact{position:absolute;right:85px;top:50px;font-family:'Montserrat',sans-serif;font-size:21px;line-height:30px;color:var(--blue);text-transform:uppercase;font-weight:500}
.header-contact .phone{color:var(--orange);font-size:26px;font-weight:600;margin-left:10px}

/* Hero */
.hero{position:relative;height:573px;background:linear-gradient(120deg,#3d7f9c 0%,#22627f 40%,#1b5673 70%,#2e7090 100%)}
.hero-photo{position:absolute;left:44px;top:30px;width:496px;height:496px;border-radius:50%;
  background:radial-gradient(circle at 35% 45%,#cfe0ec 0%,#a9c4d8 25%,#6f93ab 55%,#2f5068 85%,#1f3d52 100%)}
.hero-copy{position:absolute;left:586px;top:128px;width:600px;color:var(--white)}
.hero-title{font-family:'Montserrat',sans-serif;font-weight:700;font-size:34px;line-height:52px;color:var(--orange);text-transform:uppercase;white-space:nowrap}
.hero-text{margin-top:12px;width:540px;font-size:18.5px;line-height:27px}
.hero-arrows{position:absolute;left:786px;top:478px;display:flex;gap:12px}
.hero-arrows svg{display:block}

/* Welcome */
.welcome{height:397px;text-align:center;padding-top:56px}
.section-title{font-family:'Montserrat',sans-serif;font-weight:700;font-size:38px;line-height:48px;color:var(--blue);text-transform:uppercase}
.section-title .accent{color:var(--orange)}
.welcome-text{width:740px;margin:20px auto 0;font-size:14px;line-height:25px}
.btn-outline{display:inline-block;margin-top:28px;width:190px;height:71px;line-height:67px;border:2px solid var(--orange);color:var(--orange);font-family:'Montserrat',sans-serif;font-weight:600;font-size:20px;text-transform:uppercase}

/* Feature bands */
.feature{position:relative;height:438px}
.feature-security{background:var(--orange)}
.feature-support{background:var(--blue);height:440px}
.feature-media{position:absolute;top:0;height:100%;width:522px}
.security-media{left:77px;background:radial-gradient(circle at 50% 45%,#3f7fc4 0%,#1e4f8e 35%,#12336a 65%,#0b1f45 100%)}
.support-media{left:599px;width:524px;background:radial-gradient(circle at 60% 55%,#8a9fb4 0%,#c9d5e0 35%,#e8eef3 65%,#f7f9fb 100%)}
.feature-copy{position:absolute;color:var(--white)}
.security-copy{left:658px;top:58px;width:460px}
.support-copy{left:81px;top:58px;width:460px}
.feature-title{font-family:'Montserrat',sans-serif;font-weight:700;font-size:34px;line-height:44px;text-transform:uppercase}
.feature-text{margin-top:14px;font-size:14px;line-height:25.5px}
.btn-solid{display:block;margin-top:32px;height:68px;line-height:68px;width:188px;text-align:center;color:var(--white);font-family:'Montserrat',sans-serif;font-weight:600;font-size:20px;text-transform:uppercase}
.security-copy .btn-solid{background:var(--blue)}
.support-copy .btn-solid{background:var(--orange);margin-top:36px}

/* Testimonial */
.testimonial{height:407px;text-align:center;padding-top:62px}
.quote-mark{display:block;margin:0 auto}
.testimonial-text{width:700px;margin:22px auto 0;font-size:14px;line-height:25.5px}
.testimonial-name{margin-top:20px;font-family:'Montserrat',sans-serif;font-weight:600;font-size:19px;color:var(--blue)}
.testimonial-role{margin-top:6px;font-size:14px;color:var(--orange)}

/* News */
.news{height:541px;padding-top:50px}
.news .section-title{text-align:center}
.news-grid{display:flex;gap:16px;padding:0 77px;margin-top:44px}
.news-card{width:250px}
.news-media{height:166px;border:1px solid var(--rule)}
.news-card:nth-child(1) .news-media{background:radial-gradient(circle at 50% 55%,#8a8a8a 0%,#4a4a4a 45%,#1e1e1e 100%)}
.news-card:nth-child(2) .news-media{background:linear-gradient(100deg,#eef2f5 0%,#c6d3de 45%,#f3efe9 70%,#9aa9b6 100%)}
.news-card:nth-child(3) .news-media{background:linear-gradient(135deg,#9a9a9a 0%,#d2d2d2 40%,#6e6e6e 70%,#2e2e2e 100%)}
.news-card:nth-child(4) .news-media{background:radial-gradient(circle at 50% 60%,#3b3b3b 0%,#b8c0c6 30%,#eceff1 65%,#ffffff 100%)}
.news-title{margin-top:24px;font-family:'Montserrat',sans-serif;font-weight:700;font-size:15.5px;line-height:26px;color:var(--blue);text-transform:uppercase}
.news-card:first-child .news-title{color:var(--orange)}
.news-text{margin-top:8px;font-size:14px;line-height:26px}
.news-link{margin-top:10px;display:flex;align-items:center;gap:12px;font-family:'Montserrat',sans-serif;font-weight:700;font-size:14px;color:var(--blue);text-transform:uppercase}
.news-card:first-child .news-link{color:var(--orange)}
.news-link svg{display:block}

/* Footer */
.site-footer{height:104px;background:var(--blue);position:relative;color:var(--white);font-size:14.5px}
.footer-copy{position:absolute;left:77px;top:42px;line-height:20px}
.footer-copy strong{font-family:'Montserrat',sans-serif;text-transform:uppercase;font-weight:700}
.social{position:absolute;left:540px;top:34px;display:flex;gap:8px}
.social span{width:36px;height:36px;border-radius:50%;border:2px solid var(--white)}
.social span.active{background:var(--orange);border-color:var(--orange)}
.footer-nav{position:absolute;right:77px;top:45px;display:flex}
.footer-nav a{color:var(--white);padding:0 11px;border-left:1px solid rgba(255,255,255,.8);line-height:14px}
.footer-nav a:first-child{border-left:none}
.footer-nav a:last-child{padding-right:0}
</style>
</head>
<body>

<header class="site-header">
  <div class="brand">
    <div class="brand-name">Zorvan Lumet</div>
    <div class="brand-tagline">your IT, networks and security partner</div>
  </div>
  <div class="header-contact">Let us help you <span class="phone">1-555-014-7720</span></div>
</header>

<section class="hero" role="img" aria-label="Blue-toned server room with racks of equipment in the background">
  <div class="hero-photo" role="img" aria-label="Two IT engineers with a laptop in a server room, shown in a circular frame"></div>
  <div class="hero-copy">
    <h1 class="hero-title">Professional Powerfull<br>Security Protection</h1>
    <p class="hero-text">Lorem Ipsum is simply dummy text of the printing and typesetting industry. Lorem Ipsum has been the industry's standard dummy text ever since the 1500s.</p>
  </div>
  <div class="hero-arrows">
    <svg width="50" height="50" viewBox="0 0 50 50"><circle cx="25" cy="25" r="23" fill="none" stroke="#fff" stroke-width="2"/><path d="M28 16l-9 9 9 9" fill="none" stroke="#fff" stroke-width="3.5"/></svg>
    <svg width="50" height="50" viewBox="0 0 50 50"><circle cx="25" cy="25" r="23" fill="none" stroke="#fff" stroke-width="2"/><path d="M22 16l9 9-9 9" fill="none" stroke="#fff" stroke-width="3.5"/></svg>
  </div>
</section>

<section class="welcome">
  <h2 class="section-title">Welcome to <span class="accent">Zorvan Lumet</span></h2>
  <p class="welcome-text">Lorem Ipsum is simply dummy text of the printing and typesetting industry. Lorem Ipsum has been the industry's standard dummy text ever since the 1500s, when an unknown printer took a galley of type and scrambled it to make a type specimen book. It has survived not only five centuries, but also the leap into electronic typesetting, remaining essentially unchanged.</p>
  <a class="btn-outline">Read More</a>
</section>

<section class="feature feature-security">
  <div class="feature-media security-media" role="img" aria-label="Young man in glasses typing at a keyboard surrounded by glowing security keywords"></div>
  <div class="feature-copy security-copy">
    <h2 class="feature-title">IT Security</h2>
    <p class="feature-text">Lorem Ipsum is simply dummy text of the printing and typesetting industry. Lorem Ipsum has been the industry's standard dummy text ever since the 1500s, when an unknown printer took a galley of type and scrambled it to make a type specimen book. It has survived not only five centuries, but also the leap into electronic typesetting, remaining essentially unchanged.</p>
    <a class="btn-solid">Read More</a>
  </div>
</section>

<section class="testimonial">
  <svg class="quote-mark" width="68" height="68" viewBox="0 0 68 68"><circle cx="34" cy="34" r="32" fill="none" stroke="#165f82" stroke-width="3"/><path d="M31 24c-6 3-9 7-9 12a5 5 0 1 0 5-5c0-2 2-4 5-5zM45 24c-6 3-9 7-9 12a5 5 0 1 0 5-5c0-2 2-4 5-5z" fill="#f4583a"/></svg>
  <p class="testimonial-text">Lorem Ipsum is simply dummy text of the printing and typesetting industry. Lorem Ipsum has been the industry's standard dummy text ever since the 1500s, when an unknown printer took a galley of type and scrambled it to make a type specimen book. It has survived not only five centuries, but also the leap into electronic typesetting, remaining essentially unchanged.</p>
  <p class="testimonial-name">- Teodor Vanse</p>
  <p class="testimonial-role">Company Executive Office</p>
</section>

<section class="feature feature-support">
  <div class="feature-copy support-copy">
    <h2 class="feature-title">IT Support</h2>
    <p class="feature-text">Lorem Ipsum is simply dummy text of the printing and typesetting industry. Lorem Ipsum has been the industry's standard dummy text ever since the 1500s, when an unknown printer took a galley of type and scrambled it to make a type specimen book. It has survived not only five centuries, but also the leap into electronic typesetting, remaining essentially unchanged.</p>
    <a class="btn-solid">Read More</a>
  </div>
  <div class="feature-media support-media" role="img" aria-label="Three business people in suits working together at a laptop in a bright office"></div>
</section>

<section class="news">
  <h2 class="section-title">Latest <span class="accent">News</span></h2>
  <div class="news-grid">
    <article class="news-card">
      <div class="news-media" role="img" aria-label="Businessman holding a tablet with a support message"></div>
      <h3 class="news-title">Lorem ipsum simply dumy text printing industry</h3>
      <p class="news-text">Lorem Ipsum is simply dummy text of the printing and typesetting industry.</p>
      <a class="news-link">Read More <svg width="34" height="10" viewBox="0 0 34 10"><path d="M0 5h31M26 1l5 4-5 4" fill="none" stroke="currentColor" stroke-width="2"/></svg></a>
    </article>
    <article class="news-card">
      <div class="news-media" role="img" aria-label="Colleagues reviewing documents at a desk"></div>
      <h3 class="news-title">Lorem ipsum simply dumy text printing industry</h3>
      <p class="news-text">Lorem Ipsum is simply dummy text of the printing and typesetting industry.</p>
      <a class="news-link">Read More <svg width="34" height="10" viewBox="0 0 34 10"><path d="M0 5h31M26 1l5 4-5 4" fill="none" stroke="currentColor" stroke-width="2"/></svg></a>
    </article>
    <article class="news-card">
      <div class="news-media" role="img" aria-label="Security camera mounted on a wall"></div>
      <h3 class="news-title">Lorem ipsum simply dumy text printing industry</h3>
      <p class="news-text">Lorem Ipsum is simply dummy text of the printing and typesetting industry.</p>
      <a class="news-link">Read More <svg width="34" height="10" viewBox="0 0 34 10"><path d="M0 5h31M26 1l5 4-5 4" fill="none" stroke="currentColor" stroke-width="2"/></svg></a>
    </article>
    <article class="news-card">
      <div class="news-media" role="img" aria-label="Operator at a desk facing a wall of monitoring screens"></div>
      <h3 class="news-title">Lorem ipsum simply dumy text printing industry</h3>
      <p class="news-text">Lorem Ipsum is simply dummy text of the printing and typesetting industry.</p>
      <a class="news-link">Read More <svg width="34" height="10" viewBox="0 0 34 10"><path d="M0 5h31M26 1l5 4-5 4" fill="none" stroke="currentColor" stroke-width="2"/></svg></a>
    </article>
  </div>
</section>

<footer class="site-footer">
  <div class="footer-copy">© &nbsp;<strong>Zorvan Lumet</strong> - 2018. All Rights Reserved</div>
  <div class="social" aria-label="Social links"><span class="active"></span><span></span><span></span></div>
  <nav class="footer-nav"><a>Home</a><a>About</a><a>Services</a><a>News</a><a>Contact</a></nav>
</footer>

</body>
</html>
```